Marlow Sail Works President Business Card Carbon fiber catamarans

Hi.. I need a new business card design.. I am the President of a high tech yacht builder. We build Carbon Fiber go fast catamarans... Maybe we use the file I am sharing to you as the back of the card.. We need to look cool and crisp ...

Target Market(s)

Affluent People who will purchase a cool yacht

Industry/Entity Type

Custom Yacht Builder

Contact Information for Business Card

Dean Pellway , President, 731.508.2164 USA

Font styles to use
Serif

Requirements
Must have
• the clean crisp cool feel
Nice to have
• clean and crisp
Should not have
• Bold ugly

```html
<!DOCTYPE html>
<html lang="en">
<head>
<meta charset="utf-8">
<title>Marlow Sail Works – Business Card</title>
<link rel="stylesheet" href="https://fonts.googleapis.com/css2?family=Michroma&family=Arimo:wght@400&display=swap">
<style>
  :root {
    --stage: #2f2f2f;
    --card-dark: #0d0d0d;
    --card-mid: #262626;
    --silver: #cfcfcf;
    --silver-soft: #9a9a9a;
    --ink-dark: #1a1a1a;
    --rule: #6d6d6d;
  }
  * { margin: 0; padding: 0; box-sizing: border-box; }
  html, body {
    width: 1200px; height: 866px; overflow: hidden;
    background: var(--stage);
  }
  .stage { position: relative; width: 1200px; height: 866px; }

  .card {
    position: absolute; top: 284px;
    width: 520px; height: 298px;
    overflow: hidden;
    background: var(--card-dark);
    box-shadow: 0 14px 30px rgba(0,0,0,.55);
  }
  .card--front { left: 53px; }
  .card--back { left: 627px; }

  .card-texture {
    position: absolute; inset: 0;
    background: radial-gradient(ellipse at 45% 40%, var(--card-mid) 0%, var(--card-dark) 75%);
  }

  .wordmark {
    position: absolute;
    display: flex; align-items: center; gap: 12px;
    font-family: "Michroma", sans-serif;
    color: var(--silver);
    line-height: 1.25;
    white-space: nowrap;
  }
  .wordmark-text { display: block; }
  .wordmark-dot {
    border: 2px solid var(--silver);
    border-radius: 50%;
    flex: none;
  }
  .card--front .wordmark { right: 28px; top: 22px; font-size: 15px; letter-spacing: 3px; }
  .card--front .wordmark-dot { width: 32px; height: 32px; }
  .card--back .wordmark { left: 50%; top: 50%; transform: translate(-50%, -50%); font-size: 24px; letter-spacing: 4px; }
  .card--back .wordmark-dot { width: 46px; height: 46px; }

  .holder { position: absolute; left: 28px; top: 30px; }
  .holder-name {
    font-family: "Michroma", sans-serif;
    font-size: 13px; letter-spacing: 3px;
    color: var(--silver); text-transform: uppercase;
  }
  .holder-title {
    font-family: "Arimo", sans-serif;
    font-size: 12px; color: var(--silver-soft);
    margin-top: 4px;
  }

  .rule-top {
    position: absolute; left: 28px; top: 82px;
    width: 464px; height: 1px; background: var(--rule);
  }

  .contact-list { position: absolute; left: 28px; top: 94px; list-style: none; }
  .contact-item {
    display: flex; align-items: center; gap: 8px;
    font-family: "Arimo", sans-serif;
    font-size: 13px; color: var(--silver);
    margin-bottom: 6px;
  }
  .contact-icon { width: 13px; height: 13px; fill: var(--silver-soft); }

  .address {
    position: absolute; right: 28px; top: 214px;
    font-family: "Arimo", sans-serif;
    font-size: 13px; color: var(--silver);
  }

  .footer-band { position: absolute; left: 0; bottom: 0; width: 520px; height: 48px; }
  .website {
    position: absolute; right: 28px; bottom: 12px;
    font-family: "Arimo", sans-serif;
    font-size: 13px; color: var(--ink-dark);
  }
</style>
</head>
<body>
<main class="stage">

  <section class="card card--front" aria-label="Business card front">
    <div class="card-texture" role="img" aria-label="Carbon fibre weave texture"></div>

    <div class="holder">
      <p class="holder-name">Dean Pellway</p>
      <p class="holder-title">President</p>
    </div>

    <div class="wordmark">
      <span class="wordmark-dot"></span>
      <span class="wordmark-text">MARLOW<br>SAIL WORKS</span>
    </div>

    <div class="rule-top"></div>

    <ul class="contact-list">
      <li class="contact-item">
        <svg class="contact-icon" viewBox="0 0 24 24"><path d="M6.6 10.8a15.1 15.1 0 0 0 6.6 6.6l2.2-2.2c.3-.3.7-.4 1-.2 1.1.4 2.3.6 3.6.6.6 0 1 .4 1 1V20c0 .6-.4 1-1 1A17 17 0 0 1 3 4c0-.6.4-1 1-1h3.5c.6 0 1 .4 1 1 0 1.3.2 2.5.6 3.6.1.3 0 .7-.2 1z"/></svg>
        731.508.2164
      </li>
      <li class="contact-item">
        <svg class="contact-icon" viewBox="0 0 24 24"><path d="M2 5h20v14H2z M2 5l10 8 10-8" fill="none" stroke="#9a9a9a" stroke-width="2"/></svg>
        info@marlowsail.com
      </li>
    </ul>

    <p class="address">Rhode Island 02840, USA</p>

    <svg class="footer-band" viewBox="0 0 520 48" preserveAspectRatio="none">
      <defs>
        <linearGradient id="band-fill" x1="0" y1="0" x2="1" y2="0">
          <stop offset="0" stop-color="#a9a9a9"/>
          <stop offset="0.5" stop-color="#f2f2f2"/>
          <stop offset="1" stop-color="#d9d9d9"/>
        </linearGradient>
      </defs>
      <path d="M0 38 H250 C262 38 262 14 282 14 H520 V48 H0 Z" fill="url(#band-fill)"/>
      <path d="M0 32 H246 C258 32 260 8 280 8 H520" fill="none" stroke="#8a8a8a" stroke-width="1"/>
      <path d="M0 44 H520" stroke="#bcbcbc" stroke-width="1"/>
    </svg>
    <p class="website">www.marlowsailworks.com</p>
  </section>

  <section class="card card--back" aria-label="Business card back">
    <div class="card-texture" role="img" aria-label="Carbon fibre weave texture"></div>
    <div class="wordmark">
      <span class="wordmark-dot"></span>
      <span class="wordmark-text">MARLOW<br>SAIL WORKS</span>
    </div>
  </section>

</main>
</body>
</html>
```